Verodex business card

Business card for sustainable investment company called "Verodex". Verodex is an exchange platform selling carbon credits between buyers and sellers. Carbon Credits are an environmental commodity for reducing global carbon emissions.

the card should obviously have our logo and the theme should be sustainability/environment mixed with a trading platform.

Contact Information for Business Card

Logo, Name, Title, Phone, Email

Colors
0054AA
0677BA
7BADD7
CADEEF
E8F1F8
0094D4
00A9DD
6FCCEA
C7EBF8
E9F6FB
00AB8E
00BBA5
67D7C9
C6EFE9
E9F9F6
59FF00
82FF00
B8FF75
E3FFCB
F4FFEA

```html
<!DOCTYPE html>
<html lang="en">
<head>
<meta charset="utf-8">
<title>Verodex business card</title>
<link rel="stylesheet" href="https://fonts.googleapis.com/css2?family=Montserrat:wght@700&family=Lato:wght@400&family=Kaushan+Script&display=swap">
<style>
  :root {
    --backdrop: #1e2a36;
    --card: #e9f6fb;
    --ink: #0054aa;
    --ink-soft: #0677ba;
    --accent: #00ab8e;
    --rule: #67d7c9;
  }
  * { margin: 0; padding: 0; box-sizing: border-box; }
  html, body { width: 1200px; height: 1000px; overflow: hidden; }
  body {
    background: var(--backdrop);
    display: flex;
    flex-direction: column;
    align-items: center;
    justify-content: center;
    gap: 70px;
  }
  .card {
    width: 640px;
    height: 366px;
    background: var(--card);
    color: var(--ink);
    position: relative;
    display: flex;
    flex-direction: column;
    align-items: center;
    justify-content: center;
    overflow: hidden;
  }
  .card::after {
    content: "";
    position: absolute;
    left: 0; right: 0; bottom: 0;
    height: 8px;
    background: linear-gradient(90deg, var(--ink), var(--accent) 60%, var(--rule));
  }
  .brand {
    display: flex;
    align-items: center;
    font-family: "Montserrat", sans-serif;
    font-weight: 700;
    letter-spacing: 1px;
    text-transform: uppercase;
    color: var(--ink);
  }
  .brand-square { background: var(--accent); flex: none; }
  .card-front .brand { font-size: 46px; gap: 20px; }
  .card-front .brand-square { width: 50px; height: 50px; }
  .card-back { justify-content: flex-start; padding-top: 48px; }
  .card-back .brand { font-size: 24px; gap: 12px; letter-spacing: 2px; }
  .card-back .brand-square { width: 26px; height: 26px; }
  .person-name {
    margin-top: 34px;
    font-family: "Montserrat", sans-serif;
    font-weight: 700;
    font-size: 30px;
    letter-spacing: 12px;
    padding-left: 12px;
    text-transform: uppercase;
    color: var(--ink);
  }
  .person-title {
    font-family: "Kaushan Script", cursive;
    font-size: 24px;
    line-height: 1;
    margin-top: 4px;
    margin-left: 60px;
    color: var(--accent);
  }
  .contact {
    margin-top: 20px;
    font-family: "Lato", sans-serif;
    font-size: 18px;
    letter-spacing: 5px;
    text-align: center;
    line-height: 1.65;
    text-transform: uppercase;
    color: var(--ink-soft);
  }
  .contact .sep {
    display: inline-block;
    width: 8px; height: 8px;
    border-radius: 50%;
    background: var(--accent);
    margin: 0 10px 3px 4px;
    vertical-align: middle;
  }
</style>
</head>
<body>
  <section class="card card-front">
    <div class="brand"><span class="brand-square"></span><span class="brand-name">Verodex</span></div>
  </section>

  <section class="card card-back">
    <div class="brand"><span class="brand-square"></span><span class="brand-name">Verodex</span></div>
    <p class="person-name">Dana Corwell</p>
    <p class="person-title">manager</p>
    <div class="contact">
      <p>123-456-7890<span class="sep"></span>info@youremail.com</p>
      <p>www.yourwebsite.com</p>
    </div>
  </section>
</body>
</html>
```